Food broker, trader, wholesaler, liquidator looking for a 5 pages website

Looking for a 5 pages website design. We are food brokers, traders, wholesaler and closeout buyer working with manufacturers, distributors, importers sell to retailers, food service operators and industrial (ingredients). We help market their products. We are a resource for those who need a solution in the distribution/selling/placement of food on the shelves, kitchens and pantries. Whether we open new accounts with new products or sell short dated inventory, we know where to go and get results.

Target Market(s)

Food manufacturers, food distributors, food brokers

Coding

Coded - Design and coding required

Number of Pages Required

4 page

Font styles to use
Serif

Requirements
Must have
• Food-food production-warehouse-Food packaging-people meeting-trucks-supermarket shelves-

```html
<!DOCTYPE html>
<html lang="en">
<head>
<meta charset="utf-8">
<title>Harborline Merchant</title>
<link href="https://fonts.googleapis.com/css2?family=Esteban&family=Raleway:wght@400;500&display=swap" rel="stylesheet">
<style>
:root{
  --navy:#0c0c54;
  --navy-deep:#0a0a4a;
  --ink:#2b2b3a;
  --muted:#555;
  --white:#fff;
  --footer:#232323;
  --line:#d9d9d9;
}
*{margin:0;padding:0;box-sizing:border-box}
html,body{width:1200px;height:3617px;overflow:hidden}
body{position:relative;background:var(--white);font-family:"Esteban",serif;color:var(--ink)}
.abs{position:absolute}
/* header */
.site-header{position:absolute;left:0;top:0;width:1200px;height:108px;background:var(--white);z-index:3}
.nav a{position:absolute;top:46px;font-size:15px;color:var(--navy);text-decoration:none}
.nav a.active{border-bottom:1px solid var(--navy)}
.brand-badge{position:absolute;left:110px;top:-30px;width:204px;height:208px;border-radius:50%;background:var(--white);z-index:4;display:flex;flex-direction:column;align-items:center;justify-content:center;padding-bottom:20px}
.brand-badge .dot{width:70px;height:70px;border-radius:50%;background:var(--navy);margin-bottom:10px;margin-top:30px}
.brand-badge .name{font-size:14px;color:var(--navy);letter-spacing:.5px}
/* hero */
.hero{position:absolute;left:0;top:108px;width:1200px;height:704px;border-radius:0 0 50% 50% / 0 0 124px 124px;overflow:hidden;background:linear-gradient(100deg,#b9a68e 0%,#8a7a6a 25%,#6f7b86 50%,#a08a72 75%,#5b4f48 100%)}
.hero-panel{position:absolute;left:663px;top:222px;width:465px;height:273px;background:rgba(40,40,55,.55);padding:18px 0 0 16px;color:var(--white)}
.hero-panel h1{font-weight:400;font-size:47px;line-height:1.1}
.hero-panel p{font-size:18px;line-height:37px;margin-top:14px;width:440px}
.btn-navy{display:inline-block;background:var(--navy);color:var(--white);font-size:16px;text-align:center}
.hero-panel .btn-navy{position:absolute;left:18px;top:208px;width:131px;height:48px;line-height:48px}
/* section titles */
.sec-title{position:absolute;left:0;width:1200px;text-align:center;font-weight:400;font-size:41px;color:var(--navy)}
.sec-sub{position:absolute;left:0;width:1200px;text-align:center;font-size:16px;color:#444}
/* process */
.process-label{position:absolute;font-size:20px;line-height:34px;color:#333}
.center-name{position:absolute;left:495px;top:1268px;width:200px;text-align:center;font-size:22px;color:var(--navy)}
/* about */
.about{position:absolute;left:0;top:1663px;width:1200px;height:484px;background:var(--navy-deep)}
.about-photo{position:absolute;left:685px;top:0;width:515px;height:484px;border-radius:25% 0 0 25% / 50% 0 0 50%;background:linear-gradient(160deg,#cdbfa8 0%,#8d96a3 45%,#6d7f99 70%,#b7a58a 100%)}
.about h2{position:absolute;left:139px;top:70px;font-weight:400;font-size:45px;color:var(--white)}
.about .rule{position:absolute;left:139px;top:137px;width:60px;height:3px;background:var(--white)}
.about p{position:absolute;left:139px;top:170px;width:468px;font-size:12.5px;line-height:30px;color:var(--white);text-align:justify}
.btn-outline{position:absolute;left:139px;top:376px;width:131px;height:48px;border:1px solid var(--white);border-radius:3px;color:var(--white);font-size:14px;line-height:46px;text-align:center}
/* cards */
.card{position:absolute;top:2310px;width:309px;height:392px;background:var(--white);border:1px solid #e4e4e4;box-shadow:0 0 6px rgba(0,0,0,.08);text-align:center}
.card .ph{position:absolute;left:9px;top:10px;width:291px;height:215px}
.card h3{position:absolute;left:0;top:252px;width:100%;font-weight:400;font-size:20px;color:#222}
.card .rule{position:absolute;left:133px;top:291px;width:42px;height:2px;background:var(--navy)}
.card p{position:absolute;left:20px;top:305px;width:269px;font-family:"Raleway",sans-serif;font-size:12.5px;line-height:25px;color:#666}
/* contact */
.contact{position:absolute;left:0;top:2761px;width:1200px;height:481px;background:linear-gradient(90deg,#e8e6e2,#f1efec 40%,#e6e3de 70%,#eeece9)}
.field{position:absolute;background:var(--white);border:1px solid #cfcfcf;font-size:13px;color:#555;padding:14px 15px}
/* footer */
.footer{position:absolute;left:0;top:3242px;width:1200px;height:375px;background:var(--footer);color:var(--white)}
.foot-badge{position:absolute;left:169px;top:62px;width:140px;height:140px;border-radius:50%;background:var(--white)}
.foot-name{position:absolute;left:100px;top:196px;width:280px;text-align:center;font-size:20px;letter-spacing:.5px}
.foot-col h4{position:absolute;font-weight:400;font-size:24px;top:48px}
.foot-list{position:absolute;top:100px;list-style:none;font-family:"Raleway",sans-serif;font-size:14px}
.foot-list li{height:35px;padding-left:28px;position:relative}
.foot-list li::before{content:"»";position:absolute;left:0;top:-2px}
.news-text{position:absolute;left:836px;top:100px;width:260px;font-family:"Raleway",sans-serif;font-size:14px;line-height:24px}
.news-field{position:absolute;left:836px;top:169px;width:250px;height:42px;background:var(--white);color:#444;font-family:"Raleway",sans-serif;font-size:13px;padding:12px 14px}
.news-btn{position:absolute;left:836px;top:218px;width:95px;height:38px;background:var(--navy);color:var(--white);font-family:"Raleway",sans-serif;font-size:14px;line-height:38px;text-align:center}
.foot-rule{position:absolute;left:112px;top:298px;width:976px;height:1px;background:#444}
.copy{position:absolute;left:0;top:327px;width:1200px;text-align:center;font-family:"Raleway",sans-serif;font-size:13px}
</style>
</head>
<body>

<header class="site-header">
  <nav class="nav">
    <a class="active" style="left:584px">Home</a>
    <a style="left:671px">About Us</a>
    <a style="left:779px">What we do</a>
    <a style="left:907px">Contact</a>
    <a style="left:1007px">Giving Back</a>
  </nav>
</header>
<div class="brand-badge"><span class="dot"></span><span class="name">HARBORLINE MERCHANT</span></div>

<section class="hero" role="img" aria-label="Family shopping with a cart in a supermarket aisle">
  <div class="hero-panel">
    <h1>Harborline Merchant</h1>
    <p>Sed ut perspiciatis unde omnis iste natus error sit voluptatem accusantium doloremque laudantium, totam rem aperiam</p>
    <span class="btn-navy">Read More</span>
  </div>
</section>

<h2 class="sec-title" style="top:842px">Our Process</h2>
<p class="sec-sub" style="top:913px">Sed ut perspiciatis unde omnis iste natus error sit voluptatem accusantium doloremque</p>

<svg class="abs" style="left:0;top:960px" width="1200" height="700" viewBox="0 0 1200 700" fill="none" stroke="#0c0c54" stroke-width="2.5">
  <defs>
    <marker id="arrow" viewBox="0 0 12 12" refX="10" refY="6" markerWidth="12" markerHeight="12" orient="auto">
      <path d="M1 1 L11 6 L1 11 L4 6 Z" fill="#fff" stroke="#0c0c54" stroke-width="1.2"/>
    </marker>
  </defs>
  <g stroke-width="3.5" marker-end="url(#arrow)">
    <path d="M622 85 Q680 90 725 117"/>
    <path d="M820 200 Q850 240 862 295"/>
    <path d="M860 420 Q845 480 812 520"/>
    <path d="M708 600 Q640 625 563 623"/>
    <path d="M447 575 Q405 545 380 505"/>
    <path d="M332 395 Q328 330 336 275"/>
    <path d="M405 165 Q445 125 497 102"/>
  </g>
  <g fill="#fff">
    <circle cx="557" cy="89" r="54"/>
    <circle cx="770" cy="154" r="54"/>
    <circle cx="858" cy="355" r="54"/>
    <circle cx="762" cy="563" r="54"/>
    <circle cx="505" cy="603" r="54"/>
    <circle cx="342" cy="455" r="54"/>
    <circle cx="362" cy="216" r="54"/>
  </g>
  <g stroke-width="2">
    <!-- production machine -->
    <rect x="535" y="70" width="44" height="32" rx="2"/><circle cx="565" cy="86" r="8"/><path d="M545 102 v10 M569 102 v10 M540 112 h34"/>
    <!-- warehouse -->
    <path d="M746 150 L770 132 L794 150 V178 H746 Z"/><rect x="756" y="158" width="28" height="20"/><path d="M756 165 h28 M756 171 h28"/>
    <!-- packaging -->
    <rect x="840" y="338" width="36" height="36" rx="3"/><path d="M844 330 h28 v8 h-28 Z"/><path d="M848 356 q10 -8 20 0 q-10 8 -20 0"/>
    <!-- people -->
    <circle cx="748" cy="550" r="7"/><circle cx="762" cy="545" r="8"/><circle cx="776" cy="550" r="7"/><path d="M736 585 v-14 q12 -10 26 -8 q14 -2 26 8 v14"/>
    <!-- truck -->
    <rect x="478" y="588" width="32" height="24"/><path d="M510 596 h12 l8 8 v8 h-20"/><circle cx="488" cy="615" r="4"/><circle cx="520" cy="615" r="4"/>
    <!-- shelves -->
    <rect x="318" y="432" width="48" height="46"/><path d="M318 447 h48 M318 462 h48 M330 432 v46 M342 432 v46 M354 432 v46"/>
    <!-- food bowl -->
    <path d="M337 216 h50 q-4 20 -25 20 q-21 0 -25 -20 Z"/><path d="M348 212 q14 -20 28 0 M354 196 q-3 -6 0 -12 M362 196 q-3 -6 0 -12 M370 196 q-3 -6 0 -12"/>
  </g>
</svg>
<div class="center-name">Harborline Merchant</div>

<span class="process-label" style="left:394px;top:978px">Food<br>Production</span>
<span class="process-label" style="left:843px;top:1093px">Warehouse</span>
<span class="process-label" style="left:927px;top:1285px">Food<br>Packaging</span>
<span class="process-label" style="left:834px;top:1498px">People<br>Meeting</span>
<span class="process-label" style="left:378px;top:1563px">Trucks</span>
<span class="process-label" style="left:153px;top:1392px">Supermarket<br>Shelves</span>
<span class="process-label" style="left:245px;top:1154px">Food</span>

<section class="about">
  <div class="about-photo" role="img" aria-label="Smiling warehouse worker holding a clipboard between storage racks"></div>
  <h2>About Us</h2>
  <span class="rule"></span>
  <p>Harborline Merchant works with food manufacturers, brand owners, distributors and wholesalers market their products. Retail, Food Service and Industrial ingredients.Founded in 2008, Harborline Merchant started with the distribution of gluten free products understanding the need to provide access to unique flavors and products forthe celiac consumers. From this, we expanded into deli, dairy, groceries, frozen and beverages.</p>
  <span class="btn-outline">READ MORE</span>
</section>

<h2 class="sec-title" style="top:2187px">What We Do</h2>
<p class="sec-sub" style="top:2252px">Sed ut perspiciatis unde omnis iste natus error sit voluptatem accusantium doloremque</p>

<article class="card" style="left:112px">
  <div class="ph" role="img" aria-label="Team meeting in an office in front of a sales chart screen" style="background:linear-gradient(150deg,#2e3442,#5d6a7c 50%,#c9d2cf)"></div>
  <h3>Sales &amp; Marketing</h3><span class="rule"></span>
  <p>we connect food buyers and sellers through a dedicated approach.</p>
</article>
<article class="card" style="left:445px">
  <div class="ph" role="img" aria-label="Hands typing on a laptop beside trading screens" style="background:linear-gradient(160deg,#3a4656,#7b8a9b 45%,#c6a98a)"></div>
  <h3>Trading</h3><span class="rule"></span>
  <p>we purchase goods anywhere and ship them Nationwide and Export.</p>
</article>
<article class="card" style="left:779px">
  <div class="ph" role="img" aria-label="Two warehouse staff checking a carton and a tablet" style="background:linear-gradient(150deg,#8a7b6c,#6f87a6 50%,#c4a782)"></div>
  <h3>Closeout/Excess Inventory</h3><span class="rule"></span>
  <p>we buy closeouts and excess inventory for prisons, outlet stores and discounters.</p>
</article>

<section class="contact" role="img" aria-label="Faded warehouse interior behind the contact form">
</section>
<h2 class="sec-title" style="top:2808px">Contact Us</h2>
<p class="sec-sub" style="top:2870px">Sed ut perspiciatis unde omnis iste natus error sit voluptatem accusantium</p>
<div class="field" style="left:281px;top:2923px;width:313px;height:43px">First Name :</div>
<div class="field" style="left:605px;top:2923px;width:314px;height:43px">Last Name :</div>
<div class="field" style="left:281px;top:2980px;width:313px;height:43px">Email :</div>
<div class="field" style="left:605px;top:2980px;width:314px;height:43px">Phone :</div>
<div class="field" style="left:281px;top:3036px;width:638px;height:84px">Message :</div>
<span class="btn-navy abs" style="left:526px;top:3144px;width:148px;height:48px;line-height:48px;font-size:14px">SUBMIT</span>

<footer class="footer">
  <span class="foot-badge"></span>
  <div class="foot-name">HARBORLINE MERCHANT</div>
  <div class="foot-col"><h4 style="left:396px">Quick Links</h4></div>
  <ul class="foot-list" style="left:396px"><li>Home</li><li>About Us</li><li>What we do</li><li>Contact</li><li>Giving Back</li></ul>
  <div class="foot-col"><h4 style="left:612px">Services</h4></div>
  <ul class="foot-list" style="left:612px"><li>Sed ut perspiciatis</li><li>unde omnis iste</li><li>natus error sit</li><li>voluptatem</li><li>accusantium</li></ul>
  <div class="foot-col"><h4 style="left:836px">Newsletter</h4></div>
  <p class="news-text">Sed ut perspiciatis unde omnis iste natus error sit voluptatem</p>
  <div class="news-field">Email :</div>
  <span class="news-btn">SUBMIT</span>
  <span class="foot-rule"></span>
  <p class="copy">© Copyright 2020 Harborline Merchant.All Rights Reserved</p>
</footer>

</body>
</html>
```